Volbrey Inc Business Card

Looking to get an updated business card for a Contract Machining company (www.volbreyinc.example) - looking for a clean design the portrays the technical nature of the business - colors can follow the website design and be in any combination that makes sense (red black, white, metallic or silver) - logos attached for use also. Would like space for: Name, title, business phone (555 214-3086), cell phone , website (www.volbreyinc.example) - possibly QR code could be integrated for website (designer choice), business address - 418 Harlow Bend, Lessford, LN 48199 (cards will be for 4 employees, I will either need to modify a template or I can provide individual information)
Target Market(s)
Aerospace, defense and medical device manufacturing companies that need machining
Industry/Entity Type
Machining for aerospace, defense, medical
Contact Information for Business Card
Name, Title, Business Phone, Cell Phone, email, business website and business address
Look and feel

```html
<!DOCTYPE html>
<html lang="en">
<head>
<meta charset="utf-8">
<title>Volbrey Inc Business Card</title>
<link rel="stylesheet" href="https://fonts.googleapis.com/css2?family=Montserrat:wght@400;700&family=Arimo:wght@400&display=swap">
<style>
  :root {
    --stage: #3a3a3c;
    --card-dark: #2c2c2e;
    --card-light: #ffffff;
    --brand-red: #b51f24;
    --ink: #3d3d3d;
    --ink-soft: #7a7a7a;
    --rule: #d6d6d6;
  }
  * { box-sizing: border-box; margin: 0; padding: 0; }
  html, body { width: 1200px; height: 689px; overflow: hidden; background: var(--stage); }
  .canvas {
    width: 1200px; height: 689px; position: relative;
    display: flex; align-items: center; justify-content: center; gap: 60px;
  }
  .card {
    width: 500px; height: 286px; border-radius: 14px; position: relative; overflow: hidden;
  }
  .card--front { background: var(--card-dark); display: flex; align-items: center; justify-content: center; }
  .card--back { background: var(--card-light); }

  .brand { display: flex; flex-direction: column; align-items: center; gap: 10px; }
  .brand__disc { width: 110px; height: 110px; border-radius: 50%; background: var(--brand-red); }
  .brand__name {
    font-family: "Montserrat", sans-serif; font-weight: 700; color: var(--brand-red);
    font-size: 28px; letter-spacing: 1px; text-transform: uppercase; line-height: 1;
  }
  .card--back .brand { position: absolute; left: 40px; top: 64px; width: 180px; }
  .card--back .brand__disc { width: 96px; height: 96px; }
  .card--back .brand__name { font-size: 22px; white-space: nowrap; }

  .divider {
    position: absolute; left: 236px; top: 40px; width: 1px; height: 180px;
    background: linear-gradient(var(--card-light), var(--rule) 30%, var(--rule) 70%, var(--card-light));
  }

  .details { position: absolute; left: 258px; top: 40px; font-family: "Arimo", sans-serif; color: var(--ink); }
  .details__name { font-family: "Montserrat", sans-serif; font-weight: 700; color: var(--brand-red); font-size: 22px; line-height: 1.1; }
  .details__title { font-size: 12px; color: var(--ink-soft); margin-top: 2px; }
  .details__address { font-size: 12.5px; line-height: 1.4; margin-top: 18px; }
  .contact { list-style: none; margin-top: 14px; font-size: 12.5px; line-height: 1.55; }
  .contact li { display: flex; align-items: center; gap: 8px; }
  .contact svg { width: 11px; height: 11px; fill: var(--brand-red); flex: none; }

  .web-band {
    position: absolute; right: 0; bottom: 0; width: 220px; height: 44px;
    background: var(--brand-red);
    clip-path: polygon(16px 0, 100% 0, 100% 100%, 0 100%);
    display: flex; align-items: center; justify-content: flex-end; padding-right: 18px;
    font-family: "Arimo", sans-serif; font-size: 12.5px; color: var(--card-light);
  }
</style>
</head>
<body>
<main class="canvas">
  <section class="card card--front" aria-label="Card front">
    <div class="brand">
      <div class="brand__disc"></div>
      <div class="brand__name">Volbrey Inc</div>
    </div>
  </section>

  <section class="card card--back" aria-label="Card back">
    <div class="brand">
      <div class="brand__disc"></div>
      <div class="brand__name">Volbrey Inc</div>
    </div>
    <div class="divider"></div>
    <div class="details">
      <h1 class="details__name">Dalen Marsh</h1>
      <p class="details__title">President</p>
      <p class="details__address">418 Harlow Bend<br>Lessford, LN 48199</p>
      <ul class="contact">
        <li><svg viewBox="0 0 24 24"><path d="M6.6 10.8a15 15 0 0 0 6.6 6.6l2.2-2.2a1 1 0 0 1 1-.25 11.4 11.4 0 0 0 3.6.57 1 1 0 0 1 1 1V20a1 1 0 0 1-1 1A17 17 0 0 1 3 4a1 1 0 0 1 1-1h3.5a1 1 0 0 1 1 1c0 1.25.2 2.45.57 3.570a1 1 0 0 1-.25 1z"/></svg>555 214-3086</li>
        <li><svg viewBox="0 0 24 24"><path d="M7 1h10a2 2 0 0 1 2 2v18a2 2 0 0 1-2 2H7a2 2 0 0 1-2-2V3a2 2 0 0 1 2-2zm0 3v14h10V4zm5 15.5a1 1 0 1 0 0 2 1 1 0 0 0 0-2z"/></svg>555 307-4812</li>
        <li><svg viewBox="0 0 24 24"><path d="M2 5h20v14H2zm2 2v.5l8 5 8-5V7zm0 2.8V17h16V9.8l-8 5z"/></svg>info@volbreyinc.example</li>
      </ul>
    </div>
    <div class="web-band">www.volbreyinc.example</div>
  </section>
</main>
</body>
</html>
```